Quality Monitoring Company Needs a New Site

We are an established company that has a fair number of clients but the site lacks current design standards that we'd like to keep up with. We'd like to mimic the same style of the site on plinkora.com, vetrumo.com, https://brindlecoffer.com/, etc. We'd also like to make sure the designer understands SEO Silos and how it effects the design elements. Attached is the structure that I'd like to follow for the pages. You don't need to design every single sub-page because they'll probably be fairly similar; however, I want to see at least 1 each. Please use the content on our current site for filler areas. Please try to do a good job of understanding what we do so you can use your best judgement on what is needed to be successful. Use our color scheme and the logo should be the side view but I included the AI just in case.
Updates

I am narrowing down on the field of designs that I have received. There are a lot of similarities between the designs I like and don't like. I'd also like to ensure that some of the inner pages get done in the next 5 days so I can see the creativity that is there as well. That is probably what is next -- getting a few inner pages completed so I can see what you can come up with (not based on our current website) because the current "front pages" are all so good and so close.

Industry/Entity Type

Telecommunications

Colors

Designer to choose colors to be used in the design.

Requirements
Must have
• SEO Silo Look and Feel
• Current Colors
Should not have
• No stockphotos whatsoever. NONE.

```html
<!DOCTYPE html>
<html lang="en">
<head>
<meta charset="UTF-8">
<title>Veriqall – Sales Performance</title>
<link href="https://fonts.googleapis.com/css2?family=Poppins:wght@300;400;500;600;700&display=swap" rel="stylesheet">
<style>
  :root{
    --navy:#012d5a;
    --cyan:#07b4e7;
    --text:#5b6478;
    --nav-text:#2b3346;
    --page-bg:#f5f6fa;
    --curve-bg:#eaedf6;
    --white:#ffffff;
    --footer-line:#1d4470;
  }
  *{margin:0;padding:0;box-sizing:border-box;}
  html,body{width:1200px;height:1180px;overflow:hidden;}
  body{font-family:'Poppins',sans-serif;background:var(--page-bg);position:relative;color:var(--text);}
  .abs{position:absolute;}

  .hero-curve{position:absolute;left:0;top:0;width:1200px;height:640px;}

  .brand{left:139px;top:52px;display:flex;align-items:center;gap:8px;}
  .brand-dot{width:22px;height:22px;border-radius:50%;background:var(--cyan);}
  .brand-name{font-size:22px;font-weight:600;color:var(--navy);line-height:1;}

  .main-nav a{position:absolute;top:76px;font-size:12.5px;color:var(--nav-text);text-decoration:none;white-space:nowrap;}
  .main-nav a.is-active{color:var(--cyan);font-weight:600;}

  .call-badge{left:904px;top:64px;width:38px;height:38px;border-radius:50%;background:var(--cyan);display:flex;align-items:center;justify-content:center;}
  .call-number{left:950px;top:72px;font-size:14.5px;font-weight:700;color:var(--navy);letter-spacing:.3px;}

  .dropdown{left:443px;top:102px;width:184px;height:134px;background:var(--white);border-radius:3px;box-shadow:0 6px 18px rgba(20,40,80,.08);}
  .dropdown a{position:absolute;left:18px;font-size:11.3px;color:var(--text);text-decoration:none;white-space:nowrap;letter-spacing:.2px;}
  .dropdown .is-current{left:7px;width:170px;height:28px;top:65px;background:var(--cyan);color:var(--white);font-weight:600;padding-left:11px;line-height:28px;border-radius:2px;}

  .page-title{left:139px;top:191px;font-size:30px;font-weight:700;color:var(--navy);white-space:nowrap;}
  .page-title span{color:var(--cyan);font-weight:500;}
  .title-rule{left:139px;top:239px;width:36px;height:2px;background:var(--cyan);}

  .intro{left:143px;width:470px;font-size:11.4px;line-height:19px;color:var(--text);letter-spacing:.15px;}
  .intro-1{top:260px;}
  .intro-2{top:355px;}

  .checklist{left:143px;top:432px;list-style:none;}
  .checklist li{display:flex;align-items:center;gap:12px;height:32.3px;font-size:11.6px;color:var(--text);letter-spacing:.2px;}

  .hero-art{left:653px;top:145px;width:484px;height:428px;border-radius:12px;background:linear-gradient(135deg,#e7ecf6 0%,#d9e6f3 45%,#fbe6c6 100%);}

  .footer-band{left:0;top:806px;width:1200px;height:374px;background:var(--navy);}

  .shout{left:211px;top:700px;width:777px;height:212px;border-radius:106px;background:var(--cyan);}
  .shout-title{left:211px;top:748px;width:777px;text-align:center;font-size:43px;font-weight:400;color:var(--white);letter-spacing:.5px;}
  .shout-button{left:521px;top:827px;width:155px;height:36px;border-radius:18px;background:var(--navy);color:var(--white);font-size:13px;display:flex;align-items:center;justify-content:center;letter-spacing:.4px;}

  .footer-heading{top:966px;font-size:17px;font-weight:700;color:var(--cyan);letter-spacing:.3px;}
  .quick-links a{position:absolute;font-size:11.3px;color:var(--white);text-decoration:none;}
  .contact-line{font-size:12.8px;color:var(--white);line-height:23px;letter-spacing:.2px;}
  .footer-brand{left:940px;top:995px;font-size:28px;font-weight:600;color:var(--cyan);}
  .footer-rule{left:139px;top:1133px;width:919px;height:1px;background:var(--footer-line);}
  .copyright{left:0;top:1147px;width:1200px;text-align:center;font-size:12.4px;color:var(--white);}
</style>
</head>
<body>

<svg class="hero-curve" viewBox="0 0 1200 640" aria-hidden="true">
  <path d="M860 0 C760 140 640 320 690 460 C740 590 950 630 1200 600 L1200 0 Z" fill="var(--curve-bg)"/>
</svg>

<header>
  <div class="abs brand"><span class="brand-dot"></span><span class="brand-name">Veriqall</span></div>
  <nav class="main-nav">
    <a style="left:404px">Home</a>
    <a style="left:463px" class="is-active">Services</a>
    <a style="left:537px">Industries</a>
    <a style="left:620px">Pricing</a>
    <a style="left:683px">Team</a>
    <a style="left:742px">Blog</a>
    <a style="left:793px">Contact Us</a>
  </nav>
  <div class="abs call-badge">
    <svg width="16" height="16" viewBox="0 0 24 24"><path fill="#fff" d="M6.6 10.8a15.1 15.1 0 0 0 6.6 6.6l2.2-2.2c.3-.3.7-.4 1-.2 1.1.4 2.3.6 3.6.6.6 0 1 .4 1 1V20c0 .6-.4 1-1 1A17 17 0 0 1 3 4c0-.6.4-1 1-1h3.5c.6 0 1 .4 1 1 0 1.3.2 2.5.6 3.6.1.3 0 .7-.2 1z"/></svg>
  </div>
  <div class="abs call-number">555-014-2270</div>
</header>

<div class="abs dropdown">
  <a style="top:12px">Quality Assurance</a>
  <a style="top:39px">Coaching</a>
  <a class="is-current">Sales Performance</a>
  <a style="top:101px">Ai Enabled Voice Analytics</a>
</div>

<main>
  <h1 class="abs page-title">Sales <span>Performance</span></h1>
  <div class="abs title-rule"></div>
  <p class="abs intro intro-1">Lorem ipsum dolor sit amet, consectetuer adipiscing elit, sed diam nonummy nibh euismod tincidunt ut laoreet dolore magna aliquam erat volutpat. Ut wisi enim ad minim veniam, quis nostrud exerci tation ullamcorper suscipit lobortis nisl ut aliquip ex ea commodo consequat.</p>
  <p class="abs intro intro-2">Lorem ipsum dolor sit amet, consectetuer adipiscing elit, sed diam nonummy nibh euismod tincidunt ut laoreet dolore magna aliquam erat volutpat. Ut wisi enim ad minim veniam, quis nostrud exerci tation</p>
  <ul class="abs checklist">
    <li><svg width="11" height="9" viewBox="0 0 11 9"><path d="M1 4.5l3 3L10 1" stroke="var(--cyan)" stroke-width="2" fill="none"/></svg>Consectetuer adipiscing elit sed diam nonummy</li>
    <li><svg width="11" height="9" viewBox="0 0 11 9"><path d="M1 4.5l3 3L10 1" stroke="var(--cyan)" stroke-width="2" fill="none"/></svg>Nibh euismod tincidunt ut laoreet dolore magna</li>
    <li><svg width="11" height="9" viewBox="0 0 11 9"><path d="M1 4.5l3 3L10 1" stroke="var(--cyan)" stroke-width="2" fill="none"/></svg>Aliquam erat volutpat. Ut wisi enim ad minim veniam</li>
    <li><svg width="11" height="9" viewBox="0 0 11 9"><path d="M1 4.5l3 3L10 1" stroke="var(--cyan)" stroke-width="2" fill="none"/></svg>Quis nostrud exerci tation ullamcorper suscipit lobortis</li>
  </ul>
  <div class="abs hero-art" role="img" aria-label="Illustration of a team analysing a sales dashboard on a large monitor with charts, a magnifying glass, leaves, a shield and a padlock"></div>
</main>

<footer>
  <div class="abs footer-band"></div>
  <div class="abs shout"></div>
  <h2 class="abs shout-title">Give Us A Shout</h2>
  <a class="abs shout-button">GET IN TOUCH</a>

  <h3 class="abs footer-heading" style="left:139px">Quick Links</h3>
  <nav class="quick-links">
    <a style="left:139px;top:1004px">Home</a>
    <a style="left:139px;top:1024px">Services</a>
    <a style="left:139px;top:1044px">System Details</a>
    <a style="left:139px;top:1065px">Pricing</a>
    <a style="left:294px;top:1004px">Team</a>
    <a style="left:294px;top:1024px">Blog</a>
    <a style="left:294px;top:1044px">Contact Us</a>
    <a style="left:294px;top:1065px">Login</a>
  </nav>

  <h3 class="abs footer-heading" style="left:460px">Contact Us</h3>
  <svg class="abs" style="left:462px;top:1008px" width="11" height="15" viewBox="0 0 12 16"><path fill="#fff" d="M6 0a6 6 0 0 0-6 6c0 4.5 6 10 6 10s6-5.5 6-10a6 6 0 0 0-6-6zm0 8.5A2.5 2.5 0 1 1 6 3.5a2.5 2.5 0 0 1 0 5z"/></svg>
  <div class="abs contact-line" style="left:480px;top:1002px">4810 Harbor Crest Ave.<br>Marlow Bay, CA 90210</div>

  <svg class="abs" style="left:660px;top:1008px" width="14" height="14" viewBox="0 0 24 24"><path fill="#fff" d="M6.6 10.8a15.1 15.1 0 0 0 6.6 6.6l2.2-2.2c.3-.3.7-.4 1-.2 1.1.4 2.3.6 3.6.6.6 0 1 .4 1 1V20c0 .6-.4 1-1 1A17 17 0 0 1 3 4c0-.6.4-1 1-1h3.5c.6 0 1 .4 1 1 0 1.3.2 2.5.6 3.6.1.3 0 .7-.2 1z"/></svg>
  <div class="abs contact-line" style="left:682px;top:1002px">555-014-2270</div>
  <svg class="abs" style="left:660px;top:1044px" width="15" height="11" viewBox="0 0 16 12"><rect width="16" height="12" rx="1.5" fill="#fff"/><path d="M1 1.5l7 5 7-5" stroke="var(--navy)" stroke-width="1.4" fill="none"/></svg>
  <div class="abs contact-line" style="left:682px;top:1038px">Hello@Veriqall.com</div>

  <div class="abs footer-brand">Veriqall</div>

  <div class="abs footer-rule"></div>
  <p class="abs copyright">Copyright © 2019 VERIQALL.. All Rights Reserved.</p>
</footer>

</body>
</html>
```